BrimFalcon Business Cards

We have a defined brand. Please visit our website to get a feel for the product and the color pallets. www.brimfalcon-example.com

We need an updated, world class business card design. (See the attached existing card design). Please utilize BOTH sides of the card as shown and be creative with the layout. I do want the horse head icon to be positioned as it is with the existing card.

The remainder of the layout can be customized and I also want it vertically oriented.

Attached are the logo files and please use the colors as follows:
Green - #A5CE39
Tan - #CDBD99
Black

Feel free to play with the colors.

```html
<!DOCTYPE html>
<html lang="en">
<head>
<meta charset="utf-8">
<title>BrimFalcon Business Cards</title>
<link rel="stylesheet" href="https://fonts.googleapis.com/css2?family=Rubik:wght@400;500;700&display=swap">
<style>
  :root {
    --brand-green: #A5CE39;
    --deep-green: #3E9A3A;
    --lime: #C8D92A;
    --ink: #111111;
    --text-grey: #4a4a4a;
    --paper: #ffffff;
    --backdrop: #e9e9e6;
  }
  * { margin: 0; padding: 0; box-sizing: border-box; }
  html, body {
    width: 1200px; height: 941px; overflow: hidden;
    background: var(--backdrop);
    font-family: "Rubik", Arial, sans-serif;
  }
  .stage {
    position: relative; width: 1200px; height: 941px;
    display: flex; justify-content: center; align-items: center; gap: 70px;
  }
  .card {
    position: relative; width: 380px; height: 665px;
    box-shadow: 0 10px 30px rgba(0,0,0,.18);
    overflow: hidden;
  }
  /* Front side */
  .card--front { background: var(--paper); }
  .brand-lockup {
    position: absolute; top: 58px; left: 40px;
    display: flex; align-items: center; gap: 12px;
  }
  .brand-lockup__dot {
    width: 34px; height: 34px; border-radius: 50%; background: var(--ink);
  }
  .brand-lockup__name {
    font-size: 30px; font-weight: 500; color: var(--ink); letter-spacing: .5px;
  }
  .person {
    position: absolute; left: 0; right: 0; top: 330px; text-align: center;
  }
  .person__name { font-size: 30px; font-weight: 700; color: var(--ink); line-height: 1.1; }
  .person__role { font-size: 16px; color: var(--brand-green); margin-top: 2px; }
  .divider {
    width: 40px; height: 1.5px; background: var(--brand-green); margin: 18px auto;
  }
  .details { font-size: 16px; color: var(--text-grey); line-height: 1.3; }
  .band {
    position: absolute; left: 0; right: 0; bottom: 0; height: 14px;
    background: linear-gradient(90deg, var(--ink) 0 36%, var(--deep-green) 36%, var(--lime) 50%, var(--deep-green) 64%, var(--ink) 64% 100%);
  }
  /* Back side */
  .card--back { background: var(--brand-green); }
  .emblem {
    position: absolute; top: 110px; left: 50%; transform: translateX(-50%);
    display: flex; flex-direction: column; align-items: center; gap: 22px;
  }
  .emblem__circle { width: 230px; height: 230px; border-radius: 50%; background: var(--ink); }
  .emblem__name { font-size: 34px; font-weight: 700; color: var(--ink); }
  .tagline {
    position: absolute; left: 0; right: 0; bottom: 70px; text-align: center;
    font-size: 26px; font-weight: 700; color: var(--ink);
  }
</style>
</head>
<body>
<main class="stage">
  <section class="card card--front" aria-label="Card front">
    <div class="brand-lockup">
      <span class="brand-lockup__dot"></span>
      <span class="brand-lockup__name">BrimFalcon</span>
    </div>
    <div class="person">
      <h1 class="person__name">Dana Keller</h1>
      <p class="person__role">President &amp; CEO</p>
      <div class="divider"></div>
      <p class="details">BrimFalcon Labs LLC<br>Norwood, Ontario<br>Canada</p>
      <div class="divider"></div>
      <p class="details">555.010.2040<br>dana@brimfalcon-example.com<br>brimfalconlabs-example.com</p>
    </div>
    <div class="band"></div>
  </section>

  <section class="card card--back" aria-label="Card back">
    <div class="emblem">
      <span class="emblem__circle"></span>
      <span class="emblem__name">BrimFalcon</span>
    </div>
    <p class="tagline">Journeys Redrawn</p>
  </section>
</main>
</body>
</html>
```